Heritage Hollow Business Cards

Require a business card design. <br/><br/>Needs to include logo (either round or long version) plus these details:<br/>Maya Torvell<br/>Heritage Hollow<br/>maya@kelvadtrading.com.au<br/>02 6481 7395<br/>PO Box Glenwarra NSW 2791<br/>www.heritagehollow.com.au<br/><br/>I need in an editable format so that I can create for multiple staff members. <br/><br/>

Target Market(s)

We are an online store selling renovation products to home owners are builders. Looking for a classic classy design.

Industry/Entity Type

Home And Garden

Contact Information for Business Card

Maya Torvell
Heritage Hollow
maya@kelvadtrading.com.au
02 6481 7395
PO Box Glenwarra NSW 2791
www.heritagehollow.com.au

Colors

Designer to choose colors to be used in the design.

Requirements
Must have
• Must include Logo.

```html
<!DOCTYPE html>
<html lang="en">
<head>
<meta charset="utf-8">
<title>Heritage Hollow Business Cards</title>
<link rel="stylesheet" href="https://fonts.googleapis.com/css2?family=Libre+Baskerville&display=swap">
<style>
  :root {
    --backdrop: #e6e2dc;
    --card-dark: #221f20;
    --card-dark-edge: #2b2728;
    --card-light: #f3f3f3;
    --card-light-shade: #dcdcdc;
    --ink-dark: #2a2627;
    --ink-light: #e4e2e2;
    --ink-soft: #b9b5b5;
  }
  * { box-sizing: border-box; margin: 0; padding: 0; }
  html, body { width: 1200px; height: 780px; overflow: hidden; }
  body {
    background: var(--backdrop);
    font-family: "Libre Baskerville", "Times New Roman", serif;
    display: flex;
    align-items: center;
    justify-content: center;
    gap: 40px;
  }
  .card {
    width: 540px;
    height: 330px;
    border-radius: 4px;
    overflow: hidden;
    box-shadow: 0 10px 26px rgba(0,0,0,.22);
    position: relative;
  }

  /* Front */
  .card-front { display: flex; flex-direction: column; }
  .front-brand {
    height: 180px;
    background: linear-gradient(160deg, var(--card-light) 0%, var(--card-light-shade) 100%);
    display: flex;
    align-items: center;
    padding: 0 34px;
    gap: 18px;
  }
  .brand-mark {
    width: 70px; height: 70px;
    border: 1.5px solid var(--ink-dark);
    border-radius: 50%;
    flex: none;
  }
  .brand-name {
    color: var(--ink-dark);
    font-size: 38px;
    letter-spacing: -0.5px;
    white-space: nowrap;
  }
  .front-details {
    flex: 1;
    background: var(--card-dark);
    display: flex;
    align-items: center;
    padding: 0 30px;
  }
  .person { width: 180px; text-align: right; padding-right: 20px; }
  .person-name { color: var(--ink-light); font-size: 17px; }
  .person-title { color: var(--ink-soft); font-size: 11px; margin-top: 6px; }
  .divider { width: 1px; height: 62px; background: var(--ink-soft); flex: none; }
  .contacts { list-style: none; padding-left: 18px; }
  .contacts li {
    display: flex; align-items: center; gap: 8px;
    color: var(--ink-light); font-size: 11px; line-height: 1; margin: 6px 0;
  }
  .contacts svg { width: 14px; height: 14px; flex: none; }

  /* Back */
  .card-back {
    background: radial-gradient(ellipse at 60% 40%, var(--card-dark-edge) 0%, var(--card-dark) 75%);
    display: flex; align-items: center; justify-content: center;
  }
  .back-brand { display: flex; align-items: center; gap: 14px; }
  .back-brand .brand-mark { border-color: var(--ink-light); width: 64px; height: 64px; }
  .back-brand .brand-name { color: var(--ink-light); font-size: 30px; }
  .website {
    position: absolute; bottom: 26px; left: 0; right: 0;
    text-align: center;
    color: var(--ink-soft); font-size: 11px; letter-spacing: 3px;
  }
</style>
</head>
<body>
  <section class="card card-front" aria-label="Business card front">
    <div class="front-brand">
      <span class="brand-mark" aria-hidden="true"></span>
      <span class="brand-name">Heritage Hollow</span>
    </div>
    <div class="front-details">
      <div class="person">
        <p class="person-name">Maya Torvell</p>
        <p class="person-title">Managing Director</p>
      </div>
      <span class="divider" aria-hidden="true"></span>
      <ul class="contacts">
        <li>
          <svg viewBox="0 0 14 14" aria-hidden="true"><circle cx="7" cy="7" r="6.3" fill="none" stroke="#e4e2e2" stroke-width="1"/><path d="M4.6 3.8c.4-.3.8-.2 1 .2l.5 1c.1.3 0 .5-.2.7l-.4.3c.3.8.9 1.4 1.7 1.8l.3-.4c.2-.2.5-.3.7-.2l1 .5c.4.2.5.6.2 1-.5.7-1.2.9-2 .5-1.6-.7-2.7-1.9-3.3-3.4-.2-.8 0-1.5.5-2z" fill="#e4e2e2"/></svg>
          02 6481 7395
        </li>
        <li>
          <svg viewBox="0 0 14 14" aria-hidden="true"><circle cx="7" cy="7" r="6.3" fill="none" stroke="#e4e2e2" stroke-width="1"/><rect x="3.8" y="4.8" width="6.4" height="4.4" fill="none" stroke="#e4e2e2" stroke-width="0.9"/><path d="M3.8 4.8 7 7.3l3.2-2.5" fill="none" stroke="#e4e2e2" stroke-width="0.9"/></svg>
          maya@kelvadtrading.com.au
        </li>
        <li>
          <svg viewBox="0 0 14 14" aria-hidden="true"><circle cx="7" cy="7" r="6.3" fill="none" stroke="#e4e2e2" stroke-width="1"/><path d="M7 10.6S4.6 7.9 4.6 6.2a2.4 2.4 0 0 1 4.8 0c0 1.7-2.4 4.4-2.4 4.4z" fill="#e4e2e2"/><circle cx="7" cy="6.2" r="0.9" fill="#221f20"/></svg>
          PO Box Glenwarra NSW 2791
        </li>
      </ul>
    </div>
  </section>

  <section class="card card-back" aria-label="Business card back">
    <div class="back-brand">
      <span class="brand-mark" aria-hidden="true"></span>
      <span class="brand-name">Heritage Hollow</span>
    </div>
    <p class="website">www.heritagehollow.com.au</p>
  </section>
</body>
</html>
```